Business Card Design for Property Development Company Director

I am looking for a professional and unforgettable business card design for our Director of our Property Development Company.
Please see attached .pptx file to find out what information to include. You don't have to follow the exact format shown in the file - I am interested to see your creative flair using the information provided.

```html
<!DOCTYPE html>
<html lang="en">
<head>
<meta charset="UTF-8">
<title>Norvane Property Group – Business Card</title>
<link href="https://fonts.googleapis.com/css2?family=Arimo:wght@400;700&display=swap" rel="stylesheet">
<style>
  :root {
    --brand-blue: #1d5db3;
    --ink-grey: #5a5a5e;
    --card-white: #ffffff;
    --stage: #2b2b30;
  }
  * { box-sizing: border-box; margin: 0; padding: 0; }
  html, body { width: 1200px; height: 800px; overflow: hidden; }
  body {
    background: var(--stage);
    font-family: "Arimo", Arial, sans-serif;
    position: relative;
  }
  .card {
    position: absolute;
    width: 580px;
    height: 330px;
    left: 310px;
    background: var(--card-white);
    box-shadow: 0 10px 30px rgba(0,0,0,.4);
    overflow: hidden;
  }
  .card--front { top: 45px; }
  .card--back { top: 425px; }

  /* Front */
  .front__tagline {
    position: absolute; left: 90px; top: 62px;
    color: var(--ink-grey); font-weight: 700; font-size: 19px;
    line-height: 1.3; letter-spacing: .3px; text-transform: uppercase;
  }
  .brandmark {
    display: flex; align-items: center; gap: 14px;
  }
  .brandmark__square {
    width: 46px; height: 46px; background: var(--ink-grey); flex: none;
  }
  .brandmark__name {
    color: var(--brand-blue); font-weight: 700; font-size: 34px;
    line-height: 1; letter-spacing: .5px; text-transform: uppercase;
  }
  .brandmark__name small { display: block; font-size: 15px; letter-spacing: 3px; margin-top: 4px; }
  .front__brand { position: absolute; left: 90px; top: 150px; }
  .front__invite {
    position: absolute; left: 90px; bottom: 52px;
    color: var(--ink-grey); font-size: 13px;
  }
  .front__invite strong { font-weight: 700; }

  /* Back */
  .back__strip {
    position: absolute; left: 0; top: 0; width: 150px; height: 100%;
    display: flex; align-items: center; justify-content: center;
  }
  .back__strip .brandmark { transform: rotate(-90deg); white-space: nowrap; }
  .back__panel {
    position: absolute; left: 150px; top: 0; right: 0; bottom: 0;
    background: var(--brand-blue); color: var(--card-white);
  }
  .contact { position: absolute; left: 200px; top: 110px; }
  .contact__name { font-weight: 700; font-size: 22px; text-transform: uppercase; }
  .contact__role { font-size: 15px; margin-bottom: 14px; }
  .contact__list { list-style: none; font-size: 13px; line-height: 1.6; }
  .contact__list li { display: flex; align-items: center; gap: 8px; }
  .contact__list svg { width: 12px; height: 12px; fill: var(--card-white); flex: none; }
  .contact__licence { margin-top: 2px; }
</style>
</head>
<body>

<section class="card card--front">
  <p class="front__tagline">Property Development<br>&amp; Site Acquisition Specialists</p>
  <div class="brandmark front__brand">
    <span class="brandmark__square"></span>
    <span class="brandmark__name">Norvane<small>Property Group</small></span>
  </div>
  <p class="front__invite">Ask me about our <strong>INVESTMENT &amp; PARTNERSHIP</strong> opportunities</p>
</section>

<section class="card card--back">
  <div class="back__strip">
    <div class="brandmark">
      <span class="brandmark__square"></span>
      <span class="brandmark__name">Norvane<small>Property Group</small></span>
    </div>
  </div>
  <div class="back__panel">
    <div class="contact">
      <p class="contact__name">Daniel Whitford</p>
      <p class="contact__role">Director</p>
      <ul class="contact__list">
        <li><svg viewBox="0 0 12 12"><path d="M2.5 0.5l2 2.5-1.2 1.3a7 7 0 0 0 4.4 4.4L9 7.5l2.5 2-1.3 2C5.5 11.5 .5 6.5.5 1.8z"/></svg>0400 123 456</li>
        <li><svg viewBox="0 0 12 12"><path d="M0 2h12v8H0z M1 3l5 3.5L11 3" fill="none" stroke="#fff" stroke-width="1"/></svg>daniel@norvane.com.au</li>
        <li><svg viewBox="0 0 12 12"><circle cx="6" cy="6" r="5.5" fill="none" stroke="#fff"/><path d="M0.5 6h11M6 .5c-3 3-3 8 0 11M6 .5c3 3 3 8 0 11" fill="none" stroke="#fff" stroke-width=".8"/></svg>www.norvane.com.au</li>
        <li class="contact__licence">Real Estate Lic: 1234567 &amp; 1234568</li>
      </ul>
    </div>
  </div>
</section>

</body>
</html>
```